Business Card

THIS IS THE CARD INFORMATION
DEVELOPMENT I FINANCING I PROPERTY MANAGEMENT
DANIEL OKAFOR
3182 SW 74th Terrace
Coral Springs, FL 33076
Telephone I 855.437.2618
Facsimile I 855.437.2675
Industry/Entity Type
Business

```html
<!DOCTYPE html>
<html lang="en">
<head>
<meta charset="utf-8">
<title>Halverson Reed &amp; Company – Business Card</title>
<link rel="stylesheet" href="https://fonts.googleapis.com/css2?family=Ubuntu:wght@300;400;500;700&display=swap">
<style>
  :root {
    --page-bg: #e4e1df;
    --card-bg: #f3f1f1;
    --card-edge: #d9d5d5;
    --band-dark: #4e1846;
    --band-mid: #7a1f5e;
    --band-light: #6e2c68;
    --strip-bg: #dcd8da;
    --accent: #8b2a73;
    --ink: #2b2b2b;
    --ink-soft: #6a6868;
    --on-band: #f4eef3;
    --tagline: #e6d4e2;
    --icon-bg: #7a7878;
  }
  * { box-sizing: border-box; margin: 0; padding: 0; }
  html, body { width: 1200px; height: 1000px; overflow: hidden; }
  body {
    background: var(--page-bg);
    font-family: "Ubuntu", sans-serif;
    position: relative;
  }
  .card {
    position: absolute;
    left: 172px; top: 265px;
    width: 856px; height: 508px;
    background: var(--card-bg);
    border: 1px solid var(--card-edge);
    box-shadow: 0 10px 30px rgba(0,0,0,0.12);
  }
  .brand-band {
    position: absolute;
    left: 24px; top: 22px;
    width: 808px; height: 250px;
    background: radial-gradient(ellipse at 62% 45%, var(--band-mid) 0%, var(--band-light) 45%, var(--band-dark) 100%);
  }
  .brand-lockup {
    position: absolute;
    left: 62px; top: 56px;
    display: inline-block;
    color: var(--on-band);
    font-weight: 500;
  }
  .brand-name {
    display: block;
    font-size: 52px;
    line-height: 1;
    letter-spacing: 0.3px;
    white-space: nowrap;
  }
  .brand-sub {
    display: block;
    margin-top: 4px;
    text-align: right;
    font-size: 24px;
    line-height: 1;
  }
  .tagline {
    position: absolute;
    left: 62px; top: 180px;
    color: var(--tagline);
    font-weight: 400;
    font-size: 18px;
    letter-spacing: 0.6px;
    white-space: nowrap;
  }
  .contact-strip {
    position: absolute;
    left: 24px; top: 272px;
    width: 808px; height: 90px;
    background: var(--strip-bg);
  }
  .person-name {
    position: absolute;
    left: 78px; top: 290px;
    color: var(--accent);
    font-weight: 700;
    font-size: 24px;
    letter-spacing: 0.4px;
  }
  .person-title {
    position: absolute;
    left: 78px; top: 322px;
    color: var(--ink-soft);
    font-size: 18px;
  }
  .direct-phone {
    position: absolute;
    left: 495px; top: 292px;
    color: var(--ink);
    font-weight: 500;
    font-size: 21px;
  }
  .direct-email {
    position: absolute;
    left: 495px; top: 322px;
    color: var(--ink);
    font-size: 19px;
  }
  .address {
    position: absolute;
    left: 78px; top: 388px;
    color: var(--ink-soft);
    font-size: 21px;
    line-height: 27px;
  }
  .website {
    position: absolute;
    left: 78px; top: 459px;
    color: var(--ink-soft);
    font-size: 20px;
  }
  .office-lines {
    position: absolute;
    left: 492px; top: 388px;
    list-style: none;
  }
  .office-lines li {
    display: flex;
    align-items: center;
    height: 27px;
    color: var(--ink-soft);
    font-size: 21px;
  }
  .office-lines svg {
    width: 20px; height: 20px;
    margin-right: 16px;
  }
</style>
</head>
<body>
  <div class="card">
    <div class="brand-band">
      <div class="brand-lockup">
        <span class="brand-name">HALVERSON REED</span>
        <span class="brand-sub">&amp; COMPANY</span>
      </div>
      <div class="tagline">DEVELOPMENT&nbsp; - &nbsp;FINANCING&nbsp; - &nbsp;PROPERTY MANAGEMENT</div>
    </div>

    <div class="contact-strip"></div>
    <div class="person-name">DANIEL OKAFOR</div>
    <div class="person-title">Director</div>
    <div class="direct-phone">+359 2 418 7260</div>
    <div class="direct-email">Daniel@halversonreed.com</div>

    <div class="address">3182 SW 74th Terrace<br>Coral Springs, FL 33076</div>
    <div class="website">www.HalversonReed.com</div>

    <ul class="office-lines">
      <li>
        <svg viewBox="0 0 20 20" aria-label="Telephone">
          <rect width="20" height="20" rx="2" fill="var(--icon-bg)"/>
          <path d="M6 4.5c1 0 1.6 2.4 1.2 3-.4.5-1 .7-.7 1.4.6 1.3 1.4 2.1 2.7 2.8.6.3.9-.3 1.4-.7.6-.4 3 .2 3 1.2 0 1.3-1.3 2.6-2.8 2.300C7.6 13.7 5.3 11.4 4.5 8.2 4.1 6.4 5 4.5 6 4.5z" fill="#fff"/>
        </svg>
        855.437.2618
      </li>
      <li>
        <svg viewBox="0 0 20 20" aria-label="Facsimile">
          <rect width="20" height="20" rx="2" fill="var(--icon-bg)"/>
          <rect x="6" y="3.5" width="8" height="4" fill="#fff"/>
          <rect x="3.5" y="8" width="13" height="6" rx="1" fill="#fff"/>
          <rect x="6" y="12" width="8" height="4.5" fill="#fff" stroke="var(--icon-bg)" stroke-width="1"/>
        </svg>
        855.437.2675
      </li>
    </ul>
  </div>
</body>
</html>
```